Kelvaro.ch is looking for business card letterhead and envelope C5 with WOW effect

We need a strong business card for our company Kelvaro.ch, logo is available. You want a black or dark background on which the logo Stark r% 26 # 252; appears. Letterhead and envelope in C5 format should be in a similar design, but does not have to be We need a strong business card for our company Kelvaro.ch, logo is available. A black or dark background is desired, on which the logo Stark comes across. The letterhead and the envelope in C5 format should have a similar design.

Target Market(s)

Private customers as well as entrepreneurs

Contact Information for Business Card

E-mail: info@kelvaro-example.ch
Web.www.Kelvaro-example.ch
Tel: +41 ( 0 ) 79 482 6037
Adresse:
Lindenweg 14
9406 Tarnbach

Hier kann man Icons verwenden für Email,Tel und Adressse

Font styles to use
Other font styles liked:
• Dubai,bold

Colors

Designer to choose colors to be used in the design.

Requirements
Must have
• WOW effect
Nice to have
• R% 26 # 252; back business card with our service listings. - VEHICLE LABELING - SHOP WINDOW LABELING - STICKERS AND MUCH MORE ... in red color

```html
<!DOCTYPE html>
<html lang="en">
<head>
<meta charset="utf-8">
<title>Kelvaro.ch – Business Card</title>
<link rel="stylesheet" href="https://fonts.googleapis.com/css2?family=Arimo:wght@400;700&family=Lato:wght@400&display=swap">
<style>
  :root {
    --stage: #3d3d3d;
    --card-light: #ffffff;
    --card-dark: #0f0f0f;
    --accent: #f5c21b;
    --ink: #111111;
    --ink-light: #ffffff;
  }
  html, body {
    margin: 0;
    padding: 0;
    width: 1200px;
    height: 900px;
    overflow: hidden;
    background: var(--stage);
  }
  .canvas {
    position: relative;
    width: 1200px;
    height: 900px;
  }
  .card {
    position: absolute;
    top: 200px;
    width: 310px;
    height: 502px;
    box-shadow: 3px 4px 6px rgba(0, 0, 0, 0.45);
  }
  .card--front {
    left: 253px;
    background: var(--card-light);
    border-radius: 62px 0 62px 0;
  }
  .card--back {
    left: 627px;
    background: var(--card-dark);
    border-radius: 0 62px 0 62px;
  }

  /* Front: brand name */
  .brand {
    position: absolute;
    left: 32px;
    top: 124px;
    display: flex;
    align-items: center;
    gap: 14px;
  }
  .brand__square {
    width: 34px;
    height: 34px;
    background: var(--accent);
  }
  .brand__name {
    font-family: "Arimo", Arial, sans-serif;
    font-weight: 700;
    font-size: 25px;
    letter-spacing: 0.5px;
    color: var(--ink);
    text-transform: uppercase;
  }

  /* Front: contact list */
  .contact {
    position: absolute;
    left: 32px;
    top: 322px;
    margin: 0;
    padding: 0;
    list-style: none;
    font-family: "Arimo", Arial, sans-serif;
    font-size: 16px;
    color: var(--ink);
  }
  .contact__item {
    display: flex;
    align-items: center;
    gap: 7px;
    height: 22.5px;
  }
  .contact__item--address {
    margin-top: 20px;
  }
  .contact__icon {
    width: 18px;
    height: 18px;
    flex: none;
  }

  /* Back */
  .back-brand {
    position: absolute;
    left: 0;
    right: 0;
    top: 228px;
    text-align: center;
    font-family: "Arimo", Arial, sans-serif;
    font-weight: 700;
    font-size: 30px;
    letter-spacing: 0.5px;
    color: var(--accent);
    text-transform: uppercase;
  }
  .services {
    position: absolute;
    left: 0;
    right: 0;
    top: 385px;
    margin: 0;
    padding: 0;
    list-style: none;
    text-align: center;
    font-family: "Lato", Arial, sans-serif;
    font-size: 15px;
    line-height: 22.5px;
    color: var(--ink-light);
    text-transform: uppercase;
  }
</style>
</head>
<body>
<main class="canvas">

  <section class="card card--front" aria-label="Business card front">
    <div class="brand">
      <span class="brand__square" aria-hidden="true"></span>
      <span class="brand__name">Kelvaro.ch</span>
    </div>

    <ul class="contact">
      <li class="contact__item">
        <svg class="contact__icon" viewBox="0 0 18 18" aria-hidden="true">
          <rect x="1" y="1" width="16" height="16" rx="2" fill="none" stroke="var(--accent)" stroke-width="1.6"/>
          <path d="M6 4.5c-.8.3-1.3 1-1 2.2.8 2.9 3 5.3 5.8 6.5 1.1.4 1.9-.1 2.3-.9l-2-1.6-1.1.8c-1.3-.7-2.4-1.9-3-3.2l.8-1.1z" fill="var(--accent)"/>
        </svg>
        <span>+41 ( 0 ) 79 482 6037</span>
      </li>
      <li class="contact__item">
        <svg class="contact__icon" viewBox="0 0 18 18" aria-hidden="true">
          <rect x="0.5" y="3" width="17" height="12" fill="var(--accent)"/>
          <path d="M1 3.5 9 10l8-6.5M1 14.5l6-5M17 14.5l-6-5" fill="none" stroke="#fff" stroke-width="1.2"/>
        </svg>
        <span>info@kelvaro-example.ch</span>
      </li>
      <li class="contact__item">
        <svg class="contact__icon" viewBox="0 0 18 18" aria-hidden="true">
          <g fill="none" stroke="var(--accent)" stroke-width="1.4">
            <circle cx="9" cy="9" r="7.8"/>
            <ellipse cx="9" cy="9" rx="3.4" ry="7.8"/>
            <path d="M1.2 9h15.6M2.5 5h13M2.5 13h13"/>
          </g>
        </svg>
        <span>www.Kelvaro-example.ch</span>
      </li>
      <li class="contact__item contact__item--address">
        <svg class="contact__icon" viewBox="0 0 18 24" style="height:24px" aria-hidden="true">
          <path d="M9 1C4.6 1 1.5 4.2 1.5 8.3 1.5 13.5 9 23 9 23s7.5-9.5 7.5-14.7C16.5 4.2 13.4 1 9 1z" fill="var(--accent)"/>
          <circle cx="9" cy="8.3" r="2.8" fill="#fff"/>
        </svg>
        <span>Lindenweg 14, 9406 Tarnbach</span>
      </li>
    </ul>
  </section>

  <section class="card card--back" aria-label="Business card back">
    <div class="back-brand">Kelvaro.ch</div>
    <ul class="services">
      <li>Vehicle labeling</li>
      <li>Shop window labeling</li>
      <li>Stickers and much more ...</li>
    </ul>
  </section>

</main>
</body>
</html>
```